Home Page Website Design

The Site width is 1000 px. I've attached a Balsamiq mockup as a design layout guide. The design needs to be flat and clean. Please stick to the pixel dimensions of the mock up as the site will be responsive. I've also attached the logos used on the mockup for positional purposes.

Colours to use: Black, Grey, Green (Logo tie in) & green complementary colours.

Green (Logo tie in)
White Background
Titles: Black (Roboto Bold 700)
Text: Dark Grey (Roboto Normal 400)

Look & Style Example
http://www.brindlowe.org.uk/

Type Face
Google Fonts - Roboto

These are just guidelines, please feel free to use you own creative judgment.

Thanks

```html
<!DOCTYPE html>
<html lang="en">
<head>
<meta charset="utf-8">
<title>Ridgeway Teaching School Alliance – Home</title>
<link rel="stylesheet" href="https://fonts.googleapis.com/css2?family=Roboto:wght@400;500;700&family=Roboto+Condensed:wght@400;700&display=swap">
<style>
:root{
  --green:#1fae44;
  --green-dark:#178a35;
  --black:#111;
  --hero:#666;
  --grey-text:#555;
  --panel:#cfcfcf;
  --panel-text:#555;
  --footer:#000;
  --footer-text:#9a9a9a;
  --partners:#e4e4e4;
  --white:#fff;
}
*{box-sizing:border-box;margin:0;padding:0}
html,body{width:866px;height:1200px;overflow:hidden;background:var(--white)}
body{position:relative;font-family:"Roboto",sans-serif;color:var(--grey-text)}
.abs{position:absolute}
.cond{font-family:"Roboto Condensed",sans-serif}

/* header */
.brand{left:100px;top:26px;width:170px;text-align:center}
.brand-mark{font-family:"Roboto",sans-serif;font-weight:400;color:var(--green);font-size:50px;line-height:56px;letter-spacing:2px}
.brand-name{font-family:"Roboto",sans-serif;font-weight:400;color:var(--green);font-size:11px;margin-top:6px;white-space:nowrap}
.live-chat{left:622px;top:8px;display:flex;align-items:center;gap:8px;color:var(--green);font-family:"Roboto Condensed",sans-serif;font-size:14px}
.login{left:720px;top:0;width:67px;height:30px;background:var(--green);color:#fff;font-family:"Roboto Condensed",sans-serif;font-size:14px;display:flex;align-items:center;justify-content:center}
.register-label{left:542px;top:49px;color:var(--green);font-family:"Roboto Condensed",sans-serif;font-size:13px}
.email-field{left:542px;top:68px;width:172px;height:27px;border:1px solid #ccc;border-radius:3px;font-size:9px;color:#666;padding:8px 10px}
.submit{left:718px;top:68px;width:67px;height:27px;background:var(--green);color:#fff;border-radius:3px;font-family:"Roboto Condensed",sans-serif;font-size:13px;display:flex;align-items:center;justify-content:center}

/* nav */
.main-nav{left:0;top:122px;width:866px;height:36px;background:var(--green)}
.main-nav ul{list-style:none;display:flex;position:absolute;left:106px;top:0;height:36px}
.main-nav li{font-family:"Roboto Condensed",sans-serif;font-size:12px;color:#111;height:36px;display:flex;align-items:center;padding:0 9.5px}
.main-nav li.current{background:var(--black);color:#fff;padding:0 9px}

/* hero */
.hero{left:0;top:158px;width:866px;height:298px;background:var(--hero)}
.hero-title{left:115px;top:205px;color:#111;font-family:"Roboto Condensed",sans-serif;font-weight:700;font-size:17px}
.hero-text{left:116px;top:237px;width:250px;color:#fff;font-family:"Roboto Condensed",sans-serif;font-size:10px;line-height:21.6px}
.find-out{left:116px;top:357px;width:93px;height:34px;background:var(--black);border-radius:4px;color:#ddd;font-family:"Roboto Condensed",sans-serif;font-weight:700;font-size:12px;display:flex;align-items:center;justify-content:center}
.hero-arrows{left:113px;top:425px}
.frame{background:#fff;box-shadow:0 1px 3px rgba(0,0,0,.3)}
.frame-back1{left:400px;top:186px;width:384px;height:245px;transform:rotate(2.5deg)}
.frame-back2{left:400px;top:186px;width:382px;height:244px;transform:rotate(-2deg)}
.frame-main{left:405px;top:190px;width:373px;height:243px}
.hero-photo{left:411px;top:196px;width:361px;height:230px;background:linear-gradient(135deg,#8f8a80,#b9ae9a 45%,#6b6660)}

/* content */
.col-title{color:var(--black);font-family:"Roboto Condensed",sans-serif;font-weight:700;font-size:17px}
.welcome-title{left:90px;top:475px}
.welcome-photo{left:86px;top:505px;width:216px;height:130px;border-radius:3px;background:linear-gradient(135deg,#b7a491,#d8c6ae 50%,#8c7d70)}
.play{left:174px;top:552px}
.body-copy{font-size:9px;line-height:13px;text-align:justify;color:var(--grey-text)}
.welcome-copy1{left:86px;top:646px;width:216px}
.welcome-copy2{left:86px;top:724px;width:216px}

.training-title{left:325px;top:475px}
.training-panel{left:325px;top:505px;width:216px;height:166px;background:var(--panel);border-radius:3px;padding:6px 6px}
.training-panel ul{list-style:none}
.training-panel li{height:30.5px;border-bottom:1px solid #e8e8e8;display:flex;align-items:center;justify-content:space-between;padding:0 7px 0 8px;font-family:"Roboto Condensed",sans-serif;font-weight:700;font-size:11px;color:var(--panel-text)}
.training-panel li:last-child{border-bottom:none}
.news-title{left:327px;top:690px}
.news-item{left:325px;width:212px}
.news-item h3,.course h3{font-size:10px;font-weight:500;color:#222;line-height:13px}

.courses-title{left:566px;top:475px}
.course{left:563px;width:214px}
.course .body-copy{text-align:left;font-size:9px;color:var(--grey-text)}
.course-foot{display:flex;align-items:center;gap:17px;margin-top:11px}
.places{color:var(--green);font-size:9px}
.book{width:60px;height:24px;background:var(--black);border-radius:4px;color:var(--green);font-family:"Roboto Condensed",sans-serif;font-size:9px;display:flex;align-items:center;justify-content:center}

/* footer */
.site-footer{left:0;top:857px;width:866px;height:121px;background:var(--footer)}
.foot-list{list-style:none;font-family:"Roboto Condensed",sans-serif;font-size:9px;color:var(--footer-text);line-height:17.3px}
.follow{left:629px;top:872px;color:var(--footer-text);font-family:"Roboto Condensed",sans-serif;font-size:13px}
.social{top:871px;width:20px;height:20px}
.nts-badge{left:655px;top:901px;width:62px;height:39px;background:#fff}

/* partners */
.partners{left:0;top:978px;width:866px;height:169px;background:var(--partners)}
.partners-title{left:0;top:998px;width:866px;text-align:center;color:#555;font-family:"Roboto Condensed",sans-serif;font-size:17px}
.badge{position:absolute}
.copyright{left:0;top:1164px;width:866px;text-align:center;font-family:"Roboto Condensed",sans-serif;font-size:9.5px;color:#555}
.bottom-rule{left:90px;top:1146px;width:686px;height:3px;background:linear-gradient(to bottom,rgba(0,0,0,.12),transparent)}
</style>
</head>
<body>

<header>
  <div class="abs brand">
    <div class="brand-mark">RTA</div>
    <div class="brand-name">Ridgeway Teaching School Alliance</div>
  </div>
  <div class="abs live-chat">
    <svg width="26" height="26" viewBox="0 0 26 26" aria-hidden="true"><circle cx="13" cy="13" r="12" fill="#999"/><rect x="6" y="9" width="14" height="8" rx="4" fill="#ddd"/></svg>
    <span>Live Chat</span>
  </div>
  <div class="abs login">LOGIN</div>
  <div class="abs register-label">REGISTER NOW</div>
  <div class="abs email-field">Email Id</div>
  <div class="abs submit">SUBMIT</div>
</header>

<nav class="abs main-nav">
  <ul>
    <li class="current">HOME</li><li>ABOUT US</li><li>TRAINING &amp; DEVELOPMENT</li><li>BENEFITS</li><li>MEMEBERS</li><li>WHAT'S ON</li><li>CONTACT US</li><li>NEWS</li><li>FORUM</li>
  </ul>
</nav>

<section class="abs hero"></section>
<h1 class="abs hero-title">NEW TEACHERS IN WORKSHOP</h1>
<p class="abs hero-text">Lorem ipsum dolor sit amet, consectetur adipisicing elit, sed do eiusmod tempor incididunt ut labore et dolore magna aliqua. Ut enim ad minim veniam, quis nostrud exercitation ullamco laboris nisi ut aliquip ex ea commodo consequat. Duis aute irure dolor in reprehenderit in voluptate velit esse</p>
<div class="abs find-out">FIND OUT MORE</div>
<svg class="abs hero-arrows" width="24" height="20" viewBox="0 0 24 20" aria-hidden="true"><polygon points="8,2 2,10 8,18" fill="#fff"/><polygon points="15,2 21,10 15,18" fill="#fff"/></svg>
<div class="abs frame frame-back1"></div>
<div class="abs frame frame-back2"></div>
<div class="abs frame frame-main"></div>
<div class="abs hero-photo" role="img" aria-label="Teachers working together around tables at a workshop"></div>

<h2 class="abs col-title welcome-title">WELCOME !</h2>
<div class="abs welcome-photo" role="img" aria-label="Video still of a teacher and pupils working on the classroom floor"></div>
<svg class="abs play" width="36" height="36" viewBox="0 0 36 36" aria-hidden="true"><circle cx="18" cy="18" r="17" fill="#111"/><polygon points="15,11 24,18 15,25" fill="#fff"/></svg>
<p class="abs body-copy welcome-copy1">ed ut perspiciatis unde omnis iste natus error sit voluptatem accusantium doloremque laudantium, totam rem aperiam, eaque ipsa quae ab illo inventore veritatis et quasi architecto beatae vitae dicta sunt explicabo.</p>
<p class="abs body-copy welcome-copy2">Nemo enim ipsam voluptatem quia voluptas sit aspernatur aut odit aut fugit, sed quia consequuntur magni dolores eos qui ratione voluptatem sequi nesciunt. Neque porro quisquam est, qui dolorem ipsum quia dolor sit amet, consectetur, adipisci velit, sed quia non numquam eius modi tempora incidunt ut labore et dolore magnam aliquam quaerat voluptatem. Ut enim ad minima veniam,</p>

<h2 class="abs col-title training-title">TRAINING &amp; DEVELOPMENT</h2>
<div class="abs training-panel">
  <ul>
    <li>LEADERSHIP TRAINING<svg width="6" height="10" aria-hidden="true"><polygon points="0,0 6,5 0,10" fill="#777"/></svg></li>
    <li>CPD<svg width="6" height="10" aria-hidden="true"><polygon points="0,0 6,5 0,10" fill="#777"/></svg></li>
    <li>SCHOOL 2 SCHOOL SUPPORT<svg width="6" height="10" aria-hidden="true"><polygon points="0,0 6,5 0,10" fill="#777"/></svg></li>
    <li>RESEARCH &amp; DEVELOPMENT<svg width="6" height="10" aria-hidden="true"><polygon points="0,0 6,5 0,10" fill="#777"/></svg></li>
    <li>ITT (SCHOOL DIRECT)<svg width="6" height="10" aria-hidden="true"><polygon points="0,0 6,5 0,10" fill="#777"/></svg></li>
  </ul>
</div>
<h2 class="abs col-title news-title">LATEST NEWS</h2>
<article class="abs news-item" style="top:721px"><h3>Lorem ut perspiciatis unde omnis</h3><p class="body-copy">iste natus error sit voluptatem accusantium doloremque laudantium, totam rem aperiam, eaque ipsa quae ab illo inventore</p></article>
<article class="abs news-item" style="top:786px"><h3>Lorem ut perspiciatis unde omnis</h3><p class="body-copy">iste natus error sit voluptatem accusantium doloremque laudantium, totam rem aperiam, eaque ipsa quae ab illo inventore</p></article>

<h2 class="abs col-title courses-title">LATEST COURSES</h2>
<article class="abs course" style="top:508px"><h3>Want to Deliver consistently ‘Outstanding’ Lessons?</h3><p class="body-copy">iste natus error sit voluptatem accusantium doloremque laudantium, totam rem aperiam,</p><div class="course-foot"><span class="places">6 Places Left</span><span class="book">BOOK NOW</span></div></article>
<article class="abs course" style="top:614px"><h3>School Direct Initial Teacher Training Places Still available</h3><p class="body-copy">iste natus error sit voluptatem accusantium doloremque laudantium, totam rem aperiam,</p><div class="course-foot"><span class="places">6 Places Left</span><span class="book">BOOK NOW</span></div></article>
<article class="abs course" style="top:720px"><h3>Want to Deliver consistently ‘Outstanding’ Lessons?</h3><p class="body-copy">iste natus error sit voluptatem accusantium doloremque laudantium, totam rem aperiam,</p><div class="course-foot"><span class="places">6 Places Left</span><span class="book">BOOK NOW</span></div></article>

<footer class="abs site-footer"></footer>
<ul class="abs foot-list" style="left:87px;top:871px"><li>Ridgeway Teaching Schools Alliance</li><li>Elmfield Road</li><li>Harlow Bridge, HB4 2QT</li><li>Tel:01632 960000</li><li>Email : info@ridgewayteaching.example</li></ul>
<ul class="abs foot-list" style="left:298px;top:871px"><li>About Us</li><li>Training &amp; Development</li><li>Benefits</li><li>Members</li><li>Calendar of Events</li></ul>
<ul class="abs foot-list" style="left:470px;top:871px"><li>Contact Us</li><li>News</li><li>Forum</li><li>Site map</li></ul>
<div class="abs follow">FOLLOW US</div>
<div class="abs social" style="left:705px;background:#3b5998"></div>
<div class="abs social" style="left:730px;background:#1da1f2"></div>
<div class="abs nts-badge"></div>

<section class="abs partners"></section>
<h2 class="abs partners-title">PARTNER SCHOOLS</h2>
<svg class="abs" style="left:80px;top:1030px" width="720" height="90" viewBox="0 0 720 90" aria-hidden="true">
  <path d="M6,6 h24 v20 q0,12 -12,16 q-12,-4 -12,-16z" fill="#3a4f8a"/>
  <circle cx="66" cy="22" r="17" fill="#e9553a"/>
  <rect x="118" y="8" width="100" height="36" rx="4" fill="#b8c4dc"/>
  <rect x="241" y="8" width="54" height="56" fill="#1d3b9c"/>
  <path d="M338,6 h42 v34 q0,14 -21,22 q-21,-8 -21,-22z" fill="#1f3a6b"/>
  <path d="M418,4 h36 v28 q0,12 -18,18 q-18,-6 -18,-18z" fill="#6a4a8a"/>
  <path d="M494,10 h34 v28 q0,14 -17,22 q-17,-8 -17,-22z" fill="#2c7a3a"/>
  <path d="M566,18 h40 v34 q0,16 -20,24 q-20,-8 -20,-24z" fill="#2a4a9a"/>
  <circle cx="668" cy="34" r="28" fill="none" stroke="#1f3f7a" stroke-width="6"/>
</svg>
<div class="abs bottom-rule"></div>
<p class="abs copyright">©  Ridgeway Teaching Schools Alliance</p>

</body>
</html>
```